Luxury packaging graphic design for a new Hair care elixir

We need a packaging design for a new product for our line extension of hair colouring. We have already a packaging that is very well received (all in pink) including all accesories and transport box (attached files).
For a new product - protein for the hair - we need a different design tapping into luxury segment.

Target Market(s)

This product is mainly for women between 25-65 that are looking forward to improve hair strukture and make hair looks better, nicer, softer, healthier. The product in the packaging could be used up to 2x times.

Industry/Entity Type

Hair And Beauty

Font styles to use
Serif
Sans Serif

Colors

Designer to choose colors to be used in the design.

Requirements
Must have
• The material of the packaging are carton/styropor/and glass (attached a picture of packaging design to be adapted). The components are quite small so the packaging plays a big role to increase the value of what it is inside. The packaging needs to be inline with our actual packaging designs and corporate identity as they may be delivered together so as an assamble it should look nice, beautiful and of high quality.
• The graphic design for the different components to be adapted are:
• - grapich design for outside box
• - graphic design for the inside bottles
• - graphic design for the flyer/instructions inside the box
Nice to have
• It needs to feel that the packaging is Wow! It is going to be delivered per post so there have to be a beautiful opening effect. Eventually to work with colours like black, white and gold would give a nice luxury feeling.
• The actual product inside is a concentrated protein component so it is very small, therefore the packaging should show that even if small it is an elixir for the hair.
Should not have
• a totally diffenet look as our actual designs.

```html
<!DOCTYPE html>
<html lang="en">
<head>
<meta charset="utf-8">
<title>nola vey – Hair Elixier packaging</title>
<link rel="stylesheet" href="https://fonts.googleapis.com/css2?family=Playfair+Display:wght@700&family=Montserrat:wght@200;300;700&display=swap">
<style>
  :root {
    --paper: #ffffff;
    --box-black: #000000;
    --gold: #c9a24c;
    --gold-soft: #b8955a;
    --mark-pink: #d98ea6;
    --side-label: #111111;
  }
  * { margin: 0; padding: 0; box-sizing: border-box; }
  html, body { width: 753px; height: 1200px; overflow: hidden; background: var(--paper); }
  .sheet { position: relative; width: 753px; height: 1200px; }

  .side-label {
    position: absolute;
    font-family: "Montserrat", sans-serif;
    font-weight: 300;
    font-size: 15px;
    letter-spacing: 1px;
    color: var(--side-label);
    transform: rotate(-90deg);
    transform-origin: center;
  }
  .side-label--top { left: 28px; top: 102px; }
  .side-label--front { left: 14px; top: 500px; }

  .panel {
    position: absolute;
    background: var(--box-black);
  }
  .panel__frame {
    position: absolute;
    inset: 15px;
    border: 1.5px solid var(--gold);
  }
  .panel--top { left: 83px; top: 42px; width: 348px; height: 360px; }
  .panel--front { left: 83px; top: 425px; width: 348px; height: 753px; }

  .brand-dot {
    position: absolute;
    border-radius: 50%;
    background: var(--mark-pink);
    transform: translate(-50%, -50%);
  }

  .centered {
    position: absolute;
    left: 0; right: 0;
    text-align: center;
    white-space: nowrap;
    transform: translateY(-50%);
  }
  .brand-name {
    font-family: "Playfair Display", serif;
    font-weight: 700;
    color: var(--gold);
    line-height: 1;
  }
  .tagline {
    font-family: "Montserrat", sans-serif;
    font-weight: 700;
    font-size: 17px;
    letter-spacing: 0.5px;
    color: var(--gold);
  }
  .product-name {
    font-family: "Montserrat", sans-serif;
    font-weight: 200;
    letter-spacing: 2px;
    color: var(--gold);
  }
  .product-type {
    font-family: "Montserrat", sans-serif;
    font-weight: 200;
    color: var(--gold-soft);
  }
  .volume {
    font-family: "Montserrat", sans-serif;
    font-weight: 200;
    color: var(--gold-soft);
  }

  .panel--front .brand-name { top: 133px; font-size: 58px; }
  .panel--front .tagline { top: 181px; }
  .panel--front .product-name { top: 469px; font-size: 29px; }
  .panel--front .product-type { top: 517px; font-size: 16px; }
  .panel--front .volume { top: 688px; font-size: 15px; }

  .bottle-label {
    position: absolute;
    left: 481px; top: 780px;
    width: 219px; height: 383px;
    background: var(--box-black);
  }
  .bottle-label .brand-name { top: 52px; font-size: 40px; }
  .bottle-label .product-name { top: 228px; font-size: 20px; letter-spacing: 1.5px; }
  .bottle-label .product-type { top: 258px; font-size: 11px; }
  .bottle-label .volume { top: 315px; font-size: 11px; }
</style>
</head>
<body>
<main class="sheet">
  <span class="side-label side-label--top">TOP</span>
  <section class="panel panel--top" aria-label="Box top">
    <div class="panel__frame"></div>
    <span class="brand-dot" style="left:175px; top:177px; width:82px; height:82px;"></span>
  </section>

  <span class="side-label side-label--front">FRONT</span>
  <section class="panel panel--front" aria-label="Box front">
    <div class="panel__frame"></div>
    <p class="centered brand-name">nola vey</p>
    <p class="centered tagline">THE SHADE TO SHINE ON</p>
    <span class="brand-dot" style="left:175px; top:310px; width:82px; height:82px;"></span>
    <p class="centered product-name">HAIR ELIXIER</p>
    <p class="centered product-type">Concentrated Serum</p>
    <p class="centered volume">60mLe</p>
  </section>

  <section class="bottle-label" aria-label="Bottle label">
    <p class="centered brand-name">nola vey</p>
    <span class="brand-dot" style="left:110px; top:141px; width:54px; height:54px;"></span>
    <p class="centered product-name">HAIR ELIXIER</p>
    <p class="centered product-type">Concentrated Serum</p>
    <p class="centered volume">60mLe</p>
  </section>
</main>
</body>
</html>
```